All-Natural Head Lice Removal company

I need a business card with my pre-existing logo. We are a new company located in Portland Oregon that goes into peoples homes to help with head lice removal. My products and approach are all- natural and also will be around children.On my current logo we used Teal Bl and the color Green. I am open to new ideas just want it simple and creative

Target Market(s)

my biggest market is families of school aged children

Industry/Entity Type

Business

Contact Information for Business Card

see upload for details from previous business card

Font styles to use
Serif

Colors
33a6d7
9bcb3b
f37122

Requirements
Must have
• Basic information/ logo put into a creative format that is catching to the eye
Nice to have
• creative

```html
<!DOCTYPE html>
<html lang="en">
<head>
<meta charset="utf-8">
<title>NitNook Business Card</title>
<link href="https://fonts.googleapis.com/css2?family=Comic+Neue:wght@400;700&display=swap" rel="stylesheet">
<style>
  :root {
    --page-bg: #e9e7e3;
    --card-white: #ffffff;
    --brand-green: #9bcb3b;
    --brand-green-deep: #5fa92c;
    --brand-blue: #33a6d7;
    --brand-blue-deep: #1679b8;
    --ink: #2b2b2b;
    --text-light: #ffffff;
    --social-blue: #3b5b99;
  }
  * { margin: 0; padding: 0; box-sizing: border-box; }
  html, body { width: 1200px; height: 843px; overflow: hidden; }
  body {
    background: var(--page-bg);
    font-family: "Comic Neue", "Comic Sans MS", cursive;
    display: flex;
    flex-direction: column;
    align-items: center;
    justify-content: center;
    gap: 40px;
  }
  .card {
    width: 640px;
    height: 366px;
    border-radius: 22px;
    position: relative;
    overflow: hidden;
    box-shadow: 0 6px 18px rgba(0,0,0,0.18);
  }

  /* Back side */
  .card-back {
    background: linear-gradient(160deg, var(--brand-blue) 0%, var(--brand-blue-deep) 100%);
    display: flex;
    flex-direction: column;
    align-items: center;
    justify-content: center;
    gap: 34px;
  }
  .brand-mark {
    display: flex;
    align-items: center;
    gap: 12px;
  }
  .brand-mark .dot {
    width: 48px; height: 48px;
    border-radius: 50%;
    background: var(--brand-green);
    flex: none;
  }
  .brand-mark .name {
    font-weight: 700;
    font-size: 58px;
    color: var(--ink);
    line-height: 1;
  }
  .tagline {
    color: var(--text-light);
    text-align: center;
    font-size: 20px;
    line-height: 1.35;
  }

  /* Front side */
  .card-front {
    background: linear-gradient(90deg, var(--card-white) 0%, var(--card-white) 42%, #cfe6a4 52%, var(--brand-green) 62%, var(--brand-green-deep) 100%);
  }
  .card-front .brand-mark {
    position: absolute;
    left: 28px;
    top: 158px;
    gap: 10px;
  }
  .card-front .brand-mark .name { font-size: 44px; }
  .card-front .brand-mark .dot { width: 36px; height: 36px; }
  .illustration {
    position: absolute;
    left: 262px;
    top: 28px;
    width: 126px;
    height: 300px;
    border-radius: 63px 63px 20px 20px;
    background: linear-gradient(180deg, #8ccbea 0%, #a9d46a 50%, #c9dfa8 100%);
  }
  .social-square {
    position: absolute;
    right: 38px;
    top: 48px;
    width: 40px;
    height: 40px;
    border-radius: 6px;
    background: var(--social-blue);
  }
  .contact {
    position: absolute;
    right: 40px;
    bottom: 34px;
    width: 210px;
    text-align: right;
    color: var(--text-light);
    font-size: 19px;
    line-height: 1.35;
  }
  .contact .person {
    font-weight: 700;
    font-size: 24px;
    letter-spacing: 0.5px;
  }
  .contact .role { margin-bottom: 14px; }
</style>
</head>
<body>

  <section class="card card-back">
    <div class="brand-mark">
      <span class="dot"></span>
      <span class="name">NitNook</span>
    </div>
    <p class="tagline">Try NitNook Today, Lice Free Tomorrow!<br>All Natural Lice Removal Services</p>
  </section>

  <section class="card card-front">
    <div class="brand-mark">
      <span class="dot"></span>
      <span class="name">NitNook</span>
    </div>
    <div class="illustration" role="img" aria-label="Hand-drawn magnifying glass with a large green eye in the lens"></div>
    <div class="social-square" role="img" aria-label="Social network link"></div>
    <div class="contact">
      <p class="person">Dana Whitfield</p>
      <p class="role">Owner</p>
      <p>1-855-555-NITS (6487)</p>
      <p>dana@nitnook.com</p>
      <p>www.nitnook.com</p>
    </div>
  </section>

</body>
</html>
```